Corvana Tongue Works, LLC

We need a business card that includes information about our business and conveys a reliable business that provides document translation services and interpreters for a variety of corporate and individual clients. We want to come across as professional, reliable, yet approachable. It should include the following on one side:

ESL / ENL Language Classes, Private Lessons, and Online Tutors
PLEXA Training and Testing
Translating & Interpreting Services
Contact us about Over-the-Phone Interpreting in over 200 languages
24/7/365
www.corvanatongue.example

The other side should include (555) 481-3062

Rhoda Pelling, President
482 Garnet Ave., Ste. 219
Indianapolis, IN 40917

Please add USA as part of the address. Also, please add rmpelling@corvanatongueworks.example as the e-mail address. Thank you.

Target Market(s)

Business professionals, their families, the international community

Industry/Entity Type

Business

Contact Information for Business Card

24/7/365
www.corvanatongue.example

(555) 481-3062

Rhoda Pelling, President
482 Garnet Ave., Ste. 219
Indianapolis, IN 40917
USA

Font styles to use
Sans Serif

Colors

Designer to choose colors to be used in the design.

Requirements
Must have
• See project description
• e-mail address and web address
• Phone number
Nice to have
• a globe
• physical address
Should not have
• Should not have the same color scheme as other agencies in our market in Indiana unless it is blue and black. No purple or yellow.

```html
<!DOCTYPE html>
<html lang="en">
<head>
<meta charset="utf-8">
<title>Corvana Tongue Works – Business Card</title>
<link href="https://fonts.googleapis.com/css2?family=Work+Sans:wght@400;500;600&display=swap" rel="stylesheet">
<style>
  :root {
    --backdrop: #1e1e20;
    --card: #232325;
    --card-edge: #2c2c2e;
    --brand-grey: #9a9a9c;
    --ring: #3a3a3c;
    --text: #f2f2f2;
    --accent: #1f8fd8;
  }
  * { box-sizing: border-box; margin: 0; padding: 0; }
  html, body {
    width: 1200px; height: 900px; overflow: hidden;
    background: var(--backdrop);
    font-family: "Work Sans", Arial, sans-serif;
    color: var(--text);
  }
  .stage { position: relative; width: 1200px; height: 900px; }
  .card {
    position: absolute; left: 260px; width: 680px; height: 389px;
    background: var(--card);
    border: 1px solid var(--card-edge);
    border-radius: 3px;
    box-shadow: 0 10px 30px rgba(0,0,0,.5);
  }
  .card--back { top: 45px; }
  .card--front { top: 466px; }

  .brand { display: flex; align-items: center; gap: 14px; }
  .brand__mark {
    width: 96px; height: 96px; border-radius: 50%;
    border: 3px solid var(--ring); flex: none;
  }
  .brand__name {
    color: var(--brand-grey); font-weight: 400;
    font-size: 33px; line-height: 1.02; letter-spacing: .5px;
  }
  .brand__name small { font-size: 15px; }

  /* back side */
  .card--back .brand { position: absolute; left: 200px; top: 40px; }
  .services {
    position: absolute; left: 0; right: 0; top: 182px;
    text-align: center; font-size: 15.5px; font-weight: 500; line-height: 1.32;
  }
  .services__rule {
    width: 548px; height: 2px; background: var(--accent);
    margin: 10px auto 8px;
  }

  /* front side */
  .card--front .brand { position: absolute; left: 50px; top: 140px; }
  .card--front .brand__mark { width: 88px; height: 88px; }
  .card--front .brand__name { font-size: 30px; }
  .divider {
    position: absolute; left: 352px; top: 112px;
    width: 2px; height: 170px; background: var(--accent);
  }
  .contact { position: absolute; left: 380px; top: 118px; }
  .contact__name {
    color: var(--accent); font-size: 31px; font-weight: 500;
    letter-spacing: .5px; text-transform: uppercase; line-height: 1;
  }
  .contact__title { font-size: 17px; margin: 4px 0 14px; }
  .contact__address { font-size: 17px; line-height: 1.3; margin-bottom: 10px; }
  .contact__list { list-style: none; font-size: 17.5px; line-height: 1.3; }
  .contact__list li { display: flex; align-items: center; gap: 10px; }
  .contact__list svg { width: 12px; height: 12px; flex: none; }
</style>
</head>
<body>
<main class="stage">

  <section class="card card--back" aria-label="Card back">
    <div class="brand">
      <span class="brand__mark" aria-hidden="true"></span>
      <p class="brand__name">Corvana<br>Tongue<br>Works <small>LLC</small></p>
    </div>
    <div class="services">
      <p>ESL / ENL Language Classes, Private Lessons, and Online Tutors</p>
      <p>PLEXA Training and Testing</p>
      <p>Translating &amp; Interpreting Services</p>
      <div class="services__rule"></div>
      <p>Contact us about Over-the-Phone Interpreting in over 200 languages</p>
      <p>24/7/365</p>
    </div>
  </section>

  <section class="card card--front" aria-label="Card front">
    <div class="brand">
      <span class="brand__mark" aria-hidden="true"></span>
      <p class="brand__name">Corvana<br>Tongue<br>Works <small>LLC</small></p>
    </div>
    <div class="divider"></div>
    <div class="contact">
      <h1 class="contact__name">Rhoda Pelling</h1>
      <p class="contact__title">President</p>
      <p class="contact__address">482 Garnet Ave., Ste. 219<br>Indianapolis, IN 40917 USA</p>
      <ul class="contact__list">
        <li>
          <svg viewBox="0 0 12 12" aria-hidden="true"><path d="M3 1l2 2.5-1.2 1.2a7 7 0 0 0 3.5 3.5L8.5 7 11 9l-1.3 2C5 10.5 1.5 7 1 2.3z" fill="var(--accent)"/></svg>
          (555) 481-3062
        </li>
        <li>
          <svg viewBox="0 0 12 12" aria-hidden="true"><rect x="1" y="2.5" width="10" height="7" fill="none" stroke="var(--accent)" stroke-width="1.2"/><path d="M1 2.5l5 4 5-4" fill="none" stroke="var(--accent)" stroke-width="1.2"/></svg>
          info@corvanatongue.example
        </li>
        <li>
          <svg viewBox="0 0 12 12" aria-hidden="true"><g fill="none" stroke="var(--accent)" stroke-width="1"><circle cx="6" cy="6" r="5"/><ellipse cx="6" cy="6" rx="2.2" ry="5"/><path d="M1 6h10M2 3.3h8M2 8.7h8"/></g></svg>
          www.corvanatongue.example
        </li>
      </ul>
    </div>
  </section>

</main>
</body>
</html>
```